Kestova Information Posters for Student signage

Secondary school looking for some posters to display throughout the school with fresh designs using school colours and fitting with general feel of the school's graphic image. The final designs should be welcoming but clearly outline the required instructions. Sample designs that have been created by the school are attached with the relevant information that is required to appear on the signs. School would like a more dynamic design than the basic signs attached.
We are looking for:
- Large pop-up banner style size for the 2 posters called
"Ready for class" and "Morning Routine".
- Printable poster for the "Kestova Outdoor" sign.

Please incorporate a design feature of "the Kestova 1,2,3" into the posters and also use the Kestova Leaner values of Integrity, Compassion, Curiosity and Drive to help illustrate the content.

An option for design is to incorporate our school's first nations artwork into the design and i have also provided various extracts of design pieces that the school often uses in it's marketing materials.

Target Market(s)

Secondary School Students

Industry/Entity Type

Education

Colors
00AB8E
00BBA5
67D7C9
C6EFE9
E9F9F6
FFF300
FFF600
FEFA6F
FFFEC7
FFFEE8
FFC000
F8CF3A
FAE287
FDF2CF
FEFAEE

Requirements
Must have
• My project must have eyecatching graphics

```html
<!DOCTYPE html>
<html lang="en">
<head>
<meta charset="utf-8">
<title>Kestova Student Signage</title>
<link rel="stylesheet" href="https://fonts.googleapis.com/css2?family=Poppins:wght@500;600;700;800;900&family=Lora:ital,wght@1,600&display=swap">
<style>
:root{
  --green-dark:#1d4a22;
  --green-mid:#2f6b2c;
  --yellow:#fff200;
  --yellow-soft:#fffec7;
  --white:#ffffff;
  --page:#eceae6;
  --rule:#9a9a9a;
}
*{box-sizing:border-box;margin:0;padding:0}
html,body{width:1200px;height:800px;overflow:hidden}
body{background:var(--page);font-family:"Poppins",sans-serif;color:var(--green-dark);position:relative}

.sign{position:absolute;background:var(--white);overflow:hidden;display:flex;flex-direction:column;box-shadow:0 4px 14px rgba(0,0,0,.12)}
.sign > *{flex:none}
.banner{top:30px;width:290px;height:740px}
.banner--ready{left:70px}
.banner--routine{left:420px}
.poster{left:770px;top:150px;width:330px;height:460px}

.art-top{height:76px;background:linear-gradient(100deg,var(--yellow) 0%,var(--yellow) 55%,#fefa6f 70%,#6fa64a 88%,var(--yellow) 100%);clip-path:polygon(0 0,100% 0,100% 100%,70% 70%,40% 82%,0 55%)}
.poster .art-top{height:54px}
.art-bottom{margin-top:auto;height:96px;position:relative;background:linear-gradient(170deg,var(--white) 0%,var(--white) 22%,var(--yellow) 24%,var(--green-mid) 34%,var(--green-dark) 50%)}
.poster .art-bottom{height:82px}
.footer-values{position:absolute;right:96px;bottom:14px;text-align:right;color:var(--white);font-weight:800;font-size:11px;line-height:1.2}
.footer-values small{display:block;color:var(--yellow);font-weight:500;font-size:8.5px}
.poster .footer-values{right:92px;bottom:12px;font-size:10px}
.name-mark{position:absolute;right:12px;bottom:22px;display:flex;align-items:center;gap:4px;color:var(--yellow);font-weight:800;font-size:13px}
.name-mark::before{content:"";width:10px;height:10px;border-radius:50%;background:var(--yellow)}
.poster .name-mark{bottom:26px;font-size:12px}

.title{text-align:center;font-weight:800;line-height:1.05}
.title--ready{font-size:31px;margin:36px 10px 20px}
.title--routine{font-size:41px;font-weight:900;line-height:.88;margin:10px 0 8px;letter-spacing:-.5px}
.title--hats{font-size:16px;margin:6px 10px 10px;line-height:1.15}

.tag{display:flex;align-items:center;background:var(--yellow);border:3px solid var(--yellow);border-radius:8px;font-weight:700;white-space:nowrap}
.tag .nums{display:flex;gap:3px;background:var(--white);border-radius:0 6px 6px 0;margin-left:6px;padding:2px 4px;align-self:stretch;align-items:center}
.num{display:inline-flex;align-items:center;justify-content:center;border-radius:50%;background:var(--green-dark);color:var(--white);font-weight:700}

.panel{border:3px solid var(--yellow);border-radius:10px;margin:0 16px;position:relative}
.panel--ready{height:380px;display:flex;flex-direction:column}
.panel--ready .tag{border-radius:7px 7px 0 0;font-size:20px;padding:2px 0 2px 6px;border:none}
.panel--ready .tag .nums .num{width:23px;height:23px;font-size:14px}

.row{display:flex;align-items:center;gap:8px;border-bottom:1px dashed var(--rule);margin:0 6px}
.row:last-child{border-bottom:none}
.panel--ready .row{flex:1;gap:4px}
.row .num{flex:none}
.panel--ready .row .num{width:24px;height:24px;font-size:14px}
.icon{flex:none;border-radius:50%;background:var(--yellow);display:flex;align-items:center;justify-content:center}
.panel--ready .icon{width:68px;height:68px}
.panel--ready .label{font-size:20px;font-weight:700;line-height:.95}
.panel--ready .label small{display:block;font-size:16px;font-weight:600;margin-top:3px}

.routine-tag{margin:0 12px;font-size:19px;padding:2px 0 2px 8px}
.routine-tag .num{width:22px;height:22px;font-size:13px}
.motto{font-family:"Lora",serif;font-style:italic;font-weight:600;font-size:15px;text-align:center;margin:10px 0 18px}
.panel--list{margin:0 16px 20px;padding:12px 0 2px}
.panel-head{position:absolute;top:-13px;left:50%;transform:translateX(-50%);background:var(--yellow);border-radius:6px;font-weight:800;font-size:15px;padding:0 8px;white-space:nowrap;line-height:24px}
.panel--list .row{height:48px}
.panel--list .row .num{width:32px;height:32px;font-size:19px;margin-left:12px}
.panel--list .icon{width:32px;height:32px}
.panel--list .label{font-size:11px;font-weight:700;line-height:1.1;margin-left:8px}

.hats-tag{align-self:center;font-size:14px;padding:0 0 0 6px;border-radius:6px;position:relative;z-index:1;margin-bottom:-10px}
.hats-tag .num{width:16px;height:16px;font-size:10px}
.panel--hats{margin:0 14px;padding:10px 0 4px}
.panel--hats .row{height:52px;gap:12px;margin:0 8px}
.panel--hats .icon{width:40px;height:40px}
.panel--hats .label{font-size:28px;font-weight:900;letter-spacing:.3px}
</style>
</head>
<body>

<section class="sign banner banner--ready" aria-label="Ready for class banner">
  <div class="art-top" role="img" aria-label="Yellow and green First Nations dot artwork band"></div>
  <h1 class="title title--ready">Are you ready for class?</h1>
  <div class="panel panel--ready">
    <div class="tag">The Kestova <span class="nums"><span class="num">1</span><span class="num">2</span><span class="num">3</span></span></div>
    <div class="row">
      <span class="num">1</span>
      <span class="icon"><svg width="40" height="32" viewBox="0 0 40 32"><rect x="6" y="2" width="28" height="20" rx="2" fill="#1d4a22"/><path d="M1 25h38l-2 5H3z" fill="#1d4a22"/></svg></span>
      <span class="label">Laptop / workbook</span>
    </div>
    <div class="row">
      <span class="num">2</span>
      <span class="icon"><svg width="28" height="46" viewBox="0 0 28 46"><rect x="3" y="2" width="22" height="42" rx="7" fill="#1d4a22"/><rect x="7" y="8" width="14" height="32" rx="3" fill="none" stroke="#fff200" stroke-width="1.5"/><circle cx="14" cy="6" r="1.8" fill="#fff200"/></svg></span>
      <span class="label">Phone in Lockpouch</span>
    </div>
    <div class="row">
      <span class="num">3</span>
      <span class="icon"><svg width="48" height="30" viewBox="0 0 48 30"><path d="M14 4h20l4 16H10z" fill="#1d4a22"/><path d="M2 22q22-8 44 0l-2 5q-20-6-40 0z" fill="#1d4a22"/><rect x="11" y="15" width="26" height="2" fill="#fff200"/></svg></span>
      <span class="label">Correct uniform<small>(Including hat)</small></span>
    </div>
  </div>
  <div class="art-bottom" role="img" aria-label="Green and yellow dot artwork wave">
    <p class="footer-values">Curiosity and Drive<small>Kestova Learner Values</small></p>
    <span class="name-mark">Kestova</span>
  </div>
</section>

<section class="sign banner banner--routine" aria-label="Morning routine banner">
  <div class="art-top" role="img" aria-label="Yellow and green First Nations dot artwork band"></div>
  <h1 class="title title--routine">MORNING<br>ROUTINE</h1>
  <div class="tag routine-tag">The Kestova <span class="nums"><span class="num">1</span><span class="num">2</span><span class="num">3</span></span></div>
  <p class="motto">Early is on time, on time is late!</p>
  <div class="panel panel--list">
    <span class="panel-head">ON TIME</span>
    <div class="row"><span class="num">1</span><span class="icon"><svg width="22" height="22" viewBox="0 0 22 22"><circle cx="11" cy="11" r="9" fill="none" stroke="#1d4a22" stroke-width="2"/><path d="M11 5v6l4 3" fill="none" stroke="#1d4a22" stroke-width="2"/></svg></span><span class="label">Arrive before<br>8:30 AM</span></div>
    <div class="row"><span class="num">2</span><span class="icon"><svg width="22" height="20" viewBox="0 0 22 20"><rect x="1" y="1" width="6" height="18" fill="#1d4a22"/><rect x="8" y="1" width="6" height="18" fill="#1d4a22"/><rect x="15" y="1" width="6" height="18" fill="#1d4a22"/></svg></span><span class="label">Place Bag in<br>Locker</span></div>
    <div class="row"><span class="num">3</span><span class="icon"><svg width="20" height="20" viewBox="0 0 20 20"><rect x="4" y="2" width="2" height="16" fill="#1d4a22"/><path d="M6 2h11l-3 4 3 4H6z" fill="#1d4a22"/><rect x="1" y="17" width="18" height="2" fill="#1d4a22"/></svg></span><span class="label">Arrive at Home Group /<br>House Assembly<br>before 8:40 AM</span></div>
  </div>
  <div class="panel panel--list">
    <span class="panel-head">RUNNING LATE</span>
    <div class="row"><span class="num">1</span><span class="icon"><svg width="22" height="20" viewBox="0 0 22 20"><path d="M2 8l9-6 9 6z" fill="#1d4a22"/><rect x="3" y="9" width="16" height="10" fill="#1d4a22"/><rect x="9" y="13" width="4" height="6" fill="#fff200"/></svg></span><span class="label">Sign in at<br>Student Services</span></div>
    <div class="row"><span class="num">2</span><span class="icon"><svg width="22" height="20" viewBox="0 0 22 20"><rect x="1" y="1" width="6" height="18" fill="#1d4a22"/><rect x="8" y="1" width="6" height="18" fill="#1d4a22"/><rect x="15" y="1" width="6" height="18" fill="#1d4a22"/></svg></span><span class="label">Place bag in Locker</span></div>
    <div class="row"><span class="num">3</span><span class="icon"><svg width="20" height="20" viewBox="0 0 20 20"><rect x="4" y="1" width="12" height="18" fill="#1d4a22"/><circle cx="13" cy="10" r="1.4" fill="#fff200"/></svg></span><span class="label">Prompt arrival to<br>class expected</span></div>
  </div>
  <div class="art-bottom" role="img" aria-label="Green and yellow dot artwork wave">
    <p class="footer-values">Integrity<small>Kestova Learner Values</small></p>
    <span class="name-mark">Kestova</span>
  </div>
</section>

<section class="sign poster" aria-label="Outdoor hats poster">
  <div class="art-top" role="img" aria-label="Yellow and green First Nations dot artwork band"></div>
  <h1 class="title title--hats">We wear HATS at Kestova<br>when outdoors...</h1>
  <div class="tag hats-tag">The Kestova <span class="nums"><span class="num">1</span><span class="num">2</span><span class="num">3</span></span></div>
  <div class="panel panel--hats">
    <div class="row"><span class="icon"><svg width="24" height="20" viewBox="0 0 24 20"><path d="M2 10h14M11 4l7 6-7 6" fill="none" stroke="#1d4a22" stroke-width="3"/></svg></span><span class="label">WALKING</span></div>
    <div class="row"><span class="icon"><svg width="22" height="24" viewBox="0 0 22 24"><rect x="4" y="2" width="4" height="20" fill="#1d4a22"/><rect x="4" y="11" width="14" height="4" fill="#1d4a22"/><rect x="15" y="11" width="3" height="11" fill="#1d4a22"/></svg></span><span class="label">SITTING</span></div>
    <div class="row"><span class="icon"><svg width="24" height="24" viewBox="0 0 24 24"><circle cx="12" cy="12" r="10" fill="#1d4a22"/><path d="M2 12h20M12 2v20" stroke="#fff200" stroke-width="1.5"/></svg></span><span class="label">PLAYING</span></div>
  </div>
  <div class="art-bottom" role="img" aria-label="Green and yellow dot artwork wave">
    <p class="footer-values">Integrity<small>Kestova Learner Values</small></p>
    <span class="name-mark">Kestova</span>
  </div>
</section>

</body>
</html>
```